Podiatry clinic requires a modern revamp and editing of existing website.

I would like a fresh new look and updated information for my current business website. An easy to navigate site with prominent address and phone number for call to action. We are a podiatry clinic that focuses on general and sports podiatry.
I would like 4 pages; including Home page, About Us, Services & Contact.
www.brambleridgepodiatry.net

Target Market(s)

Active working professionals.

Industry/Entity Type

Medical

Coding

Coded - Design and coding required

Number of Pages Required

4 page

Font styles to use
Sans Serif

Colors
6b449b

Requirements
Must have
• A modern look with logo and active images; clean and uncluttered. Visible phone number and address for call to action.
• 4 pages - Home, About Us, Services, Contact.
• Home page - update address & service logos.
• About Us - update of personal information.
• Services - Revamp of existing page.
• Contact page to include Google map, email & phone number.
Nice to have
• Ability to add content easily; eg. a blog or adding video onto Home page.
• Link to Facebook page.

```html
<!DOCTYPE html>
<html lang="en">
<head>
<meta charset="utf-8">
<title>Bramble Ridge Podiatry</title>
<link href="https://fonts.googleapis.com/css2?family=Raleway:wght@300;400;500&family=Arimo:wght@400;700&family=Roboto+Condensed:wght@400;700&display=swap" rel="stylesheet">
<style>
:root{
  --purple:#6b449b;
  --purple-soft:#9b82bf;
  --navy:#2f2a5e;
  --orange:#f7791f;
  --green:#8cc63f;
  --charcoal:#333;
  --grey-bar:#666;
  --text:#333;
  --rule:#ddd;
  --white:#fff;
}
*{box-sizing:border-box;margin:0;padding:0}
html,body{width:1200px;height:2214px;overflow:hidden}
body{position:relative;background:var(--white);font-family:"Arimo",Arial,sans-serif;color:var(--text)}
.abs{position:absolute}

/* hero */
.hero{left:0;top:0;width:1200px;height:511px;background:linear-gradient(180deg,#9fb0c6 0%,#8a9a86 30%,#5f6b4e 45%,#6d6a66 60%,#585653 100%)}
.social-top{top:9px;display:flex;gap:24px;left:896px}
.social-top span{width:20px;height:20px;border-radius:50%;border:2px solid rgba(255,255,255,.85)}
.header-bar{left:125px;top:34px;width:944px;height:81px;background:rgba(255,255,255,.92)}
.brand-box{left:125px;top:34px;width:142px;height:81px;background:var(--purple-soft);display:flex;align-items:center;gap:8px;padding:0 10px}
.brand-box .dot,.footer-brand .dot{width:14px;height:14px;border-radius:50%;background:var(--white);flex:none}
.brand-name{font-family:"Raleway",sans-serif;font-weight:500;font-size:15px;line-height:17px;color:var(--white)}
.nav{left:546px;top:34px;height:81px;display:flex;font-size:14px;color:#444}
.nav a{display:flex;align-items:center;padding:0 14px;text-decoration:none;color:inherit}
.nav a.active{background:var(--orange);color:var(--white);padding:0 13px}
.nav-divider{left:868px;top:50px;width:2px;height:52px;background:#555}
.call{left:900px;top:58px;display:flex;align-items:center;gap:10px}
.call-label{color:var(--orange);font-size:14px;line-height:16px}
.call-number{font-size:19px;color:#222;line-height:22px}
.arrow{top:244px;width:52px;height:51px;background:rgba(200,200,200,.55);display:flex;align-items:center;justify-content:center}
.headline-top{left:267px;top:244px;height:42px;padding:0 11px;background:var(--orange);color:var(--white);font-family:"Roboto Condensed",sans-serif;font-size:25px;line-height:42px}
.headline-top b{font-weight:700}
.headline-bottom{left:267px;top:292px;height:42px;padding:0 11px;background:var(--navy);color:var(--white);font-family:"Roboto Condensed",sans-serif;font-size:25px;line-height:42px}
.slider-dots{left:528px;top:497px;display:flex;gap:4px}
.slider-dots span{width:36px;height:5px;background:rgba(255,255,255,.45)}
.slider-dots span.on{background:var(--white)}

/* welcome */
.section-title{width:1200px;left:0;text-align:center;font-family:"Raleway",sans-serif;font-weight:400;color:#222}
.section-title::after{content:"";display:block;width:200px;height:1px;background:var(--rule);margin:10px auto 0}
.welcome-title{top:551px;font-size:29px}
.welcome-copy{left:148px;top:600px;width:904px;text-align:center;font-size:15px;line-height:27px;color:#333}
.welcome-cta{left:0;top:721px;width:1200px;text-align:center;font-weight:700;font-size:15px;line-height:25px;color:#111}
.divider-shadow{left:0;top:806px;width:1200px;height:14px;background:radial-gradient(ellipse at 50% 0%,rgba(0,0,0,.25),rgba(0,0,0,0) 70%)}

/* services */
.services-title{top:850px;font-size:29px}
.service-card{top:920px;width:298px;height:199px;box-shadow:0 2px 6px rgba(0,0,0,.25)}
.service-card h3{height:48px;background:#666;color:var(--white);font-family:"Raleway",sans-serif;font-weight:400;font-size:21px;line-height:48px;text-align:center}
.service-photo{height:151px;border:3px solid #9fd3ef;border-top:none}
.service-text{top:1138px;width:298px;text-align:center;font-size:13.5px;line-height:25px;color:#333}

/* affiliations */
.affiliations{left:0;top:1259px;width:1200px;height:229px;background:var(--purple-soft)}
.aff-title{top:1290px;font-size:31px;color:#333}
.aff-title::after{background:rgba(255,255,255,.4)}
.badge{top:1367px;width:206px;height:80px;background:var(--white);border:1px solid #ccc;display:flex;align-items:center;justify-content:center}
.badge span{width:150px;height:40px;border-radius:6px;background:#e4e0ec}

/* news & video */
.col-title{font-family:"Raleway",sans-serif;font-weight:400;font-size:32px;color:#222;border-bottom:1px solid var(--rule);padding-bottom:8px}
.news-title{left:133px;top:1516px;width:437px}
.video-title{left:632px;top:1516px;width:435px}
.news-item{left:124px;width:440px;display:flex;gap:24px}
.news-date{width:72px;height:65px;color:var(--white);text-align:center;flex:none}
.news-date .day{font-size:36px;line-height:42px}
.news-date .mon{font-size:16px;line-height:18px;letter-spacing:1px}
.d-orange{background:var(--orange)}
.d-dark{background:#333}
.d-dark .mon{color:#555}
.d-green{background:var(--green)}
.news-item h4{font-family:"Raleway",sans-serif;font-weight:500;font-size:19px;color:var(--navy);line-height:22px;margin-top:2px}
.news-item p{font-size:13.5px;line-height:19px;color:#555;margin-top:6px}
.video-frame{left:642px;top:1604px;width:375px;height:265px;background:var(--white);box-shadow:0 1px 6px rgba(0,0,0,.3)}
.video-screen{left:22px;top:20px;width:331px;height:221px;background:linear-gradient(135deg,#e9ecef,#c9c2b8 50%,#3d4452);border:1px solid #222}
.play{left:142px;top:78px;width:48px;height:36px;background:rgba(0,0,0,.8);border-radius:4px;display:flex;align-items:center;justify-content:center}
.controls{left:0;bottom:0;width:331px;height:30px;background:linear-gradient(#3a3a3a,#111);display:flex;align-items:center;gap:10px;padding:0 10px}
.progress{flex:1;height:5px;background:#555;border-radius:3px;position:relative}
.progress i{position:absolute;left:0;top:0;width:45%;height:5px;background:#d21c1c;border-radius:3px}

/* footer */
.footer{left:0;top:1919px;width:1200px;height:251px;background:var(--purple-soft);color:#222}
.footer h5{font-family:"Raleway",sans-serif;font-weight:500;font-size:18px;color:#444;margin-bottom:14px}
.f-links{left:133px;top:1942px;width:180px}
.f-links li{list-style:none;font-size:13.5px;line-height:24.5px;padding-left:16px;position:relative}
.f-links li::before{content:"›";position:absolute;left:2px;color:#555}
.f-vline{top:1980px;width:1px;height:170px;background:rgba(255,255,255,.35)}
.f-contact{left:356px;top:1942px;width:250px}
.f-row{display:flex;gap:12px;font-size:13.5px;line-height:17px;padding:7px 0 14px;border-bottom:1px solid rgba(255,255,255,.3);margin-bottom:8px}
.f-row:last-child{border:none}
.f-hours{left:692px;top:1942px;width:175px}
.f-hours p{font-size:13.5px;line-height:18px;padding:6px 0 12px;border-bottom:1px solid rgba(255,255,255,.3)}
.f-hours p:last-child{border:none}
.footer-brand{left:908px;top:2005px;display:flex;align-items:center;gap:10px}
.footer-brand .brand-name{font-size:22px;line-height:26px}
.bottom-bar{left:0;top:2170px;width:1200px;height:44px;background:var(--grey-bar);display:flex;align-items:center;justify-content:space-between;padding:0 108px 0 130px;color:var(--white);font-size:13.5px}
.bottom-social{display:flex;gap:9px}
.bottom-social span{width:34px;height:34px;border-radius:50%;background:#bbb}
</style>
</head>
<body>

<!-- hero -->
<div class="abs hero" role="img" aria-label="Runner's legs and running shoes on a park path at morning"></div>
<div class="abs social-top" aria-label="Social links"><span></span><span></span><span></span><span></span></div>
<div class="abs header-bar"></div>
<div class="abs brand-box"><span class="dot"></span><span class="brand-name">Bramble Ridge Podiatry</span></div>
<nav class="abs nav">
  <a class="active" href="#">Home</a><a href="#">About Us</a><a href="#">Services</a><a href="#">Contact</a>
</nav>
<div class="abs nav-divider"></div>
<div class="abs call">
  <svg width="28" height="28" viewBox="0 0 28 28"><circle cx="14" cy="14" r="12.5" fill="none" stroke="#333" stroke-width="1.5"/><path d="M10 8c1-1 2 0 3 2s0 2-1 3c1 2 2 3 4 4 1-1 1-2 3-1s3 2 2 3c-2 2-5 2-8-1s-5-6-3-10z" fill="#333"/></svg>
  <div><div class="call-label">Call Us Today</div><div class="call-number">1300 482 907</div></div>
</div>
<div class="abs arrow" style="left:0"><svg width="22" height="22" viewBox="0 0 22 22"><path d="M11 4 4 11l7 7M18 4l-7 7 7 7" fill="none" stroke="#fff" stroke-width="2"/></svg></div>
<div class="abs arrow" style="left:1148px"><svg width="22" height="22" viewBox="0 0 22 22"><path d="m11 4 7 7-7 7M4 4l7 7-7 7" fill="none" stroke="#fff" stroke-width="2"/></svg></div>
<div class="abs headline-top"><b>Bramble Ridge Podiatry</b> is a Podiatry clinic in the</div>
<div class="abs headline-bottom">Heart of Melbourne CBD</div>
<div class="abs slider-dots"><span class="on"></span><span></span><span></span></div>

<!-- welcome -->
<h1 class="abs section-title welcome-title">Welcome to Bramble Ridge Podiatry</h1>
<p class="abs welcome-copy">Bramble Ridge Podiatry is a Podiatry clinic in the heart of Melbourne CBD. We are located between Alder &amp; Finch Streets in the Harbourline Business Centre / Linden Hotel Complex. Our podiatrists are fully qualified health professionals who are able to diagnose, treat, manage or help to prevent all medical conditions that affect the feet and lower limb. We provide General Podiatry Treatment and some Specialised Services in relation to various foot conditions, including Sports Injuries, Orthotic Therapy and Nail Surgery.</p>
<p class="abs welcome-cta">For Appointments or Enquiries please<br>call us on 1300 482 907 &nbsp;or email: &nbsp;info@brambleridgepodiatry.net</p>
<div class="abs divider-shadow"></div>

<!-- services -->
<h2 class="abs section-title services-title">Our Services</h2>
<div class="abs service-card" style="left:134px"><h3>Sports Injuries</h3><div class="service-photo" role="img" aria-label="Basketball player holding an injured ankle on court" style="background:linear-gradient(135deg,#e8d8c8,#c9875a 55%,#5a4a40)"></div></div>
<div class="abs service-card" style="left:452px"><h3>Orthotic Therapy</h3><div class="service-photo" role="img" aria-label="Podiatrist fitting an orthotic insole to a patient's foot" style="background:linear-gradient(135deg,#d9dde0,#b49e85 55%,#6b665f)"></div></div>
<div class="abs service-card" style="left:769px"><h3>Nail Surgery</h3><div class="service-photo" role="img" aria-label="Gloved hands giving a local anaesthetic injection to a toe" style="background:linear-gradient(135deg,#cfd4d8,#d8c2ad 55%,#3a3a3a)"></div></div>
<p class="abs service-text" style="left:134px">Lorem ipsum dolor sit amet, consectetuer<br>adipiscing elit, sed diam nonummy nibh<br>euismod tincidunt ut laoreet.</p>
<p class="abs service-text" style="left:452px">Lorem ipsum dolor sit amet, consectetuer<br>adipiscing elit, sed diam nonummy nibh<br>euismod tincidunt ut laoreet.</p>
<p class="abs service-text" style="left:769px">Lorem ipsum dolor sit amet, consectetuer<br>adipiscing elit, sed diam nonummy nibh<br>euismod tincidunt ut laoreet.</p>

<!-- affiliations -->
<section class="abs affiliations"></section>
<h2 class="abs section-title aff-title">Our Affiliations</h2>
<div class="abs badge" style="left:153px" aria-label="Affiliation badge"><span></span></div>
<div class="abs badge" style="left:378px" aria-label="Affiliation badge"><span></span></div>
<div class="abs badge" style="left:604px" aria-label="Affiliation badge"><span></span></div>
<div class="abs badge" style="left:828px" aria-label="Affiliation badge"><span></span></div>

<!-- news -->
<h2 class="abs col-title news-title">Recent News</h2>
<h2 class="abs col-title video-title">Our Video</h2>
<article class="abs news-item" style="top:1594px"><div class="news-date d-orange"><div class="day">03</div><div class="mon">Aug</div></div><div><h4>Lorem ipsum dolor</h4><p>Lorem ipsum dolor sit amet, consectetuer adipiscing elit, sed diam nonummy nibh euismod</p></div></article>
<article class="abs news-item" style="top:1697px"><div class="news-date d-dark"><div class="day">01</div><div class="mon">Aug</div></div><div><h4>Lorem ipsum dolor</h4><p>Lorem ipsum dolor sit amet, consectetuer adipiscing elit, sed diam nonummy nibh euismod</p></div></article>
<article class="abs news-item" style="top:1800px"><div class="news-date d-green"><div class="day">01</div><div class="mon">Aug</div></div><div><h4>Lorem ipsum dolor</h4><p>Lorem ipsum dolor sit amet, consectetuer adipiscing elit, sed diam nonummy nibh euismod</p></div></article>

<!-- video -->
<div class="abs video-frame">
  <div class="abs video-screen" role="img" aria-label="Video still of a couple shaking hands with a consultant">
    <div class="abs play"><svg width="16" height="18" viewBox="0 0 16 18"><path d="M2 1l13 8-13 8z" fill="#fff"/></svg></div>
    <div class="abs controls">
      <svg width="10" height="12" viewBox="0 0 10 12"><path d="M1 1l8 5-8 5z" fill="#fff"/></svg>
      <svg width="14" height="12" viewBox="0 0 14 12"><path d="M1 4h3l4-3v10L4 8H1z" fill="#fff"/><path d="M10 3q3 3 0 6" stroke="#fff" fill="none"/></svg>
      <div class="progress"><i></i></div>
      <svg width="12" height="12" viewBox="0 0 12 12"><path d="M1 5V1h4M7 1h4v4M11 7v4H7M5 11H1V7" stroke="#fff" fill="none" stroke-width="1.5"/></svg>
    </div>
  </div>
</div>

<!-- footer -->
<footer class="abs footer"></footer>
<div class="abs f-links"><h5>Quick Links</h5><ul><li>Consulting</li><li>Inspections</li><li>Training</li><li>General Contracing</li><li>Clients</li><li>Contact Us</li></ul></div>
<div class="abs f-vline" style="left:314px"></div>
<div class="abs f-contact"><h5>Contact Details</h5>
  <div class="f-row"><svg width="12" height="16" viewBox="0 0 12 16"><path d="M6 0a6 6 0 0 1 6 6c0 4-6 10-6 10S0 10 0 6a6 6 0 0 1 6-6z" fill="#222"/><circle cx="6" cy="6" r="2.2" fill="#9b82bf"/></svg><span>Suite 214 / 62 Ridgeway<br>Street Melbourne 3000</span></div>
  <div class="f-row"><svg width="14" height="14" viewBox="0 0 14 14"><path d="M3 1c1-1 2 0 3 2s0 2-1 3c1 2 2 3 3 3 1-1 1-2 3-1s2 2 1 3c-2 2-5 1-8-2S1 3 3 1z" fill="#222"/></svg><span>1300 482 907</span></div>
  <div class="f-row"><svg width="14" height="10" viewBox="0 0 14 10"><rect width="14" height="10" fill="#222"/><path d="M0 0l7 6 7-6" stroke="#9b82bf" fill="none"/></svg><span>info@brambleridgepodiatry.net</span></div>
</div>
<div class="abs f-vline" style="left:620px"></div>
<div class="abs f-hours"><h5>Hours of Operation</h5>
  <p>Monday to Friday<br>10:00am to 07:00pm</p>
  <p>Saturday<br>10:00am to 05:00pm</p>
  <p>Sunday<br>By Appointment Only</p>
</div>
<div class="abs footer-brand"><span class="dot"></span><span class="brand-name">Bramble Ridge<br>Podiatry</span></div>
<div class="abs bottom-bar"><span>Copyright © 2016 Northgate Web Services. &nbsp;All Right Reserved.</span><div class="bottom-social" aria-label="Social links"><span></span><span></span><span></span></div></div>

</body>
</html>
```